fernwick study hub community

The website presents a new interactive learning system where it provides not only the teaching material as the instructor friend who can both teach and learn, making friends and making money.
Make friends and get money.

```html
<!DOCTYPE html>
<html lang="en">
<head>
<meta charset="utf-8">
<title>Fernwick Study Hub</title>
<link rel="stylesheet" href="https://fonts.googleapis.com/css2?family=PT+Sans:wght@400;700&family=Arimo:wght@400;700&family=Exo+2:ital,wght@1,800&display=swap">
<style>
:root{
  --navy:#04132e;
  --blue:#0a8ee0;
  --text:#333;
  --muted:#8b8b8b;
  --rule:#d6d6d6;
  --white:#fff;
}
*{box-sizing:border-box;margin:0;padding:0}
html,body{width:992px;height:1200px;overflow:hidden;background:var(--white)}
body{position:relative;font-family:"PT Sans",sans-serif;color:var(--text)}
.header{position:absolute;left:0;top:0;width:992px;height:78px;background:var(--navy);border-top:3px solid var(--blue)}
.brand{position:absolute;left:78px;top:24px;color:var(--white);font:700 21px/1 "PT Sans",sans-serif;letter-spacing:1px;display:flex;align-items:center;gap:8px}
.brand-dot{width:14px;height:14px;border-radius:50%;background:var(--blue)}
.social-top{position:absolute;left:558px;top:31px;display:flex;gap:17px}
.social-top span{width:14px;height:14px;border-radius:50%;background:#c9d0db}
.search{position:absolute;left:684px;top:24px;width:226px;height:32px;background:#0b1c3a;border-radius:2px;color:#d8dde6;font-size:11px;padding:9px 17px}
.search svg{position:absolute;right:12px;top:7px}
.nav{position:absolute;left:0;top:78px;width:992px;height:46px;background:linear-gradient(#fff,#f2f2f2);border-bottom:2px solid #dcdcdc;display:flex;padding-left:82px}
.nav a{display:block;height:44px;line-height:44px;padding:0 10px;font-size:11px;color:#222;text-decoration:none;text-transform:uppercase}
.nav a.active{background:var(--blue);color:var(--white);padding:0 11px}
.hero{position:absolute;left:82px;top:145px;width:828px;height:407px;background:linear-gradient(180deg,#7a5a44,#8d6a4e 50%,#6a4a36)}
.hero-caption{position:absolute;left:0;bottom:0;width:100%;height:61px;background:rgba(20,20,20,.45)}
.hero-caption h2{position:absolute;left:29px;top:18px;color:var(--white);font:italic 800 21px/1 "Exo 2",sans-serif}
.hero-arrows{position:absolute;right:30px;top:20px}
.section-title{position:absolute;font:700 18px/1 "Arimo",sans-serif;color:#444;text-transform:uppercase;display:flex;align-items:center;gap:14px}
.section-title::after{content:"";flex:1;height:4px;border-top:1px solid var(--rule);border-bottom:1px solid var(--rule)}
.welcome-img{position:absolute;left:82px;top:620px;width:152px;height:110px;background:linear-gradient(135deg,#c7a67f,#e0d2bf 60%,#5a6c87)}
.welcome-text{position:absolute;left:263px;top:617px;width:387px;font:400 10px/17px "Arimo",sans-serif;color:var(--muted);text-align:justify}
.field{position:absolute;left:690px;width:220px;height:33px;border:1px solid #cfcfcf;font:11px "Arimo",sans-serif;color:#888;padding:10px 16px}
.btn{position:absolute;left:690px;top:702px;width:70px;height:28px;background:var(--blue);color:var(--white);font:700 11px/28px "Arimo",sans-serif;text-align:center}
.card{position:absolute;top:814px;width:254px}
.card-img{position:relative;height:114px}
.date{position:absolute;right:0;bottom:-10px;width:32px;height:34px;background:var(--blue);color:var(--white);font:700 10px/11px "PT Sans",sans-serif;text-align:center;padding-top:6px}
.card h3{margin-top:22px;font:700 11px/1 "PT Sans",sans-serif;color:#111}
.card .meta{margin-top:7px;font-size:8.5px;color:var(--muted)}
.card p{margin-top:6px;font-size:9px;line-height:17px;color:#555}
.footer{position:absolute;left:0;top:1078px;width:992px;height:122px;background:var(--navy);border-bottom:5px solid var(--blue);color:var(--white)}
.footer-nav{position:absolute;left:82px;top:38px;font-size:9px;text-transform:uppercase}
.footer-nav span{margin:0 8px}
.copy{position:absolute;left:82px;top:67px;font-size:10px}
.social-foot{position:absolute;left:789px;top:47px;display:flex;gap:10px}
.social-foot span{width:23px;height:23px}
</style>
</head>
<body>
<header class="header">
  <div class="brand"><span>FERNWICK STUDY HUB</span><span class="brand-dot"></span></div>
  <div class="social-top" aria-label="Social links"><span></span><span></span><span></span><span></span></div>
  <div class="search">Search Here ...
    <svg width="18" height="18" viewBox="0 0 18 18"><circle cx="7" cy="7" r="5.5" fill="none" stroke="#0a8ee0" stroke-width="2"/><line x1="11" y1="11" x2="16" y2="16" stroke="#0a8ee0" stroke-width="2.5"/></svg>
  </div>
</header>
<nav class="nav">
  <a class="active">Home</a><a>Who we are</a><a>Lidc news</a><a>Be a friend instructor</a><a>Gives your suggetion</a><a>Fernwick</a><a>Report your findings</a><a>Create your goute</a><a>Contact</a>
</nav>
<section class="hero" role="img" aria-label="Photo of two students studying on a wooden bench with books and a laptop">
  <div class="hero-caption">
    <h2>BY MAKING FRIENDS YOU CAN MAKE MONEY</h2>
    <svg class="hero-arrows" width="36" height="20" viewBox="0 0 36 20"><polyline points="12,2 4,10 12,18" fill="none" stroke="#fff" stroke-width="3"/><polyline points="24,2 32,10 24,18" fill="none" stroke="#fff" stroke-width="3"/></svg>
  </div>
</section>
<h2 class="section-title" style="left:82px;top:582px;width:563px">Welcome to Fernwick</h2>
<div class="welcome-img" role="img" aria-label="Photo of students working together around a table"></div>
<p class="welcome-text">Lorem ipsum dolor sit amet, consectetuer adipiscing elit. Aenean commodo ligula eget dolor. Aenean massa. Cum sociis natoque penatibus et magnis dis parturient montes, nascetur ridiculus mus. Donec quam felis, ultricies nec, pellentesque eu, pretium quis, sem. Nulla consequat massa quis enim. Donec pede justo, fringilla vel, aliquet nec, vulputate eget, arcu. In enim justo, rhoncus ut, imperdiet a, venenatis vitae, justo. Nullam dictum felis eu pede mollis pretium. Integer tincidunt. Cras dapibus. Vivamus elementum semper nisi. Aenean vulputate eleifend tellus. Aenean leo ligula, porttitor eu</p>
<h2 class="section-title" style="left:690px;top:582px;width:220px">Login</h2>
<div class="field" style="top:618px">User Name</div>
<div class="field" style="top:660px">Password</div>
<div class="btn">LOGIN</div>
<h2 class="section-title" style="left:80px;top:771px;width:830px">Latest News</h2>
<article class="card" style="left:82px">
  <div class="card-img" role="img" aria-label="Photo of a group of students holding books" style="background:linear-gradient(90deg,#c9a46a,#e8c35a 40%,#d9d2c8 70%,#e0663a)"><div class="date">21<br>Dec</div></div>
  <h3>Eiusmod tempor incidunt ipsumdol</h3>
  <div class="meta">By Ann Marlow | 3 Comments | Fit Row</div>
  <p>Lorem ipsum dolor sit amet, consectetur adipisici elit, sed eiusmod tempor incidunt ut labore et dolore magna aliqua. Idque Caesaris facere voluntate liceret: sese habere....</p>
</article>
<article class="card" style="left:368px">
  <div class="card-img" role="img" aria-label="Photo of an audience seated in a lecture hall" style="background:linear-gradient(180deg,#8a7e78,#5f5a60 50%,#2f3340)"><div class="date">21<br>Dec</div></div>
  <h3>Eiusmod tempor incidunt ipsumdol</h3>
  <div class="meta">By Ann Marlow | 3 Comments | Fit Row</div>
  <p>Lorem ipsum dolor sit amet, consectetur adipisici elit, sed eiusmod tempor incidunt ut labore et dolore magna aliqua. Idque Caesaris facere voluntate liceret: sese habere....</p>
</article>
<article class="card" style="left:656px">
  <div class="card-img" role="img" aria-label="Photo of cheerful young people giving thumbs up" style="background:linear-gradient(90deg,#d9b28a,#c98f6e 50%,#6f7a55)"><div class="date">21<br>Dec</div></div>
  <h3>Eiusmod tempor incidunt ipsumdol</h3>
  <div class="meta">By Ann Marlow | 3 Comments | Fit Row</div>
  <p>Lorem ipsum dolor sit amet, consectetur adipisici elit, sed eiusmod tempor incidunt ut labore et dolore magna aliqua. Idque Caesaris facere voluntate liceret: sese habere....</p>
</article>
<footer class="footer">
  <div class="footer-nav">Home<span>|</span>Who we are<span>|</span>Lidc news<span>|</span>Be a friend instructor<span>|</span>Gives your suggetion<span>|</span>Create your goute<span>|</span>Contact</div>
  <div class="copy">Copyright © 2014 &nbsp;interactive learning system named Fernwick Study Hub | &nbsp;All rights reserved</div>
  <div class="social-foot" aria-label="Social links">
    <span style="background:#3b5998"></span><span style="background:#2aa3e0"></span><span style="background:#d6402d"></span><span style="background:#f39c12"></span>
  </div>
</footer>
</body>
</html>
```